"Tidewater Sleeve" - Envelope Package for 3 Small Pamphlets/Tracts

We need a design for an envelope package that will be folded to fit 3 small tracts/pamphlets. The final product will be paper that is simply folded - not glued or stapled. The tracts/pamphlets themselves are the ones that can be found at www.vantirocanada.ca/literature - they don't need to be designed as we already have them in print. We just want a package/envelope to put them in so we can hand them out in a creative way.

We are looking for a few different ideas to choose from - which is why we are coming to you! Attached is a design brief that outlines the desired format and pictures of mocked-finished product. Also attached is the "G" (VANTIRO logo). One of the pictures will provide you with the final product measurement in millimetres. You will have to add safety margins for full bleed to send to the printer. This needs to be designed in Photoshop or Illustrator. Photoshop is preferred.

Although I like the white background because it looks clean, please also provide a darker background to see if the "wallet" effect would work. (I am talking about the outside of the package. the inside should remain white.)

I like the concept of the icons for body and mind, but the icon for "spirit" should be something like a generic sunrise, sunset or peaceful lake.

You will notice that there are "folding" numbers inside the attached mockup picture. We would like them to be nicely designed on the final product so that people know how to fold the envelope, but those numbers should be hidden behind the flaps/pamphlets once the 3 pamphlets are in and the product is fully folded. We would also like to have light grey dotted lines to know where to fold on the inside of the package.

On the centre back panel is where you have the question that states "Know someone who needs healing?"

```html
<!DOCTYPE html>
<html lang="en">
<head>
<meta charset="utf-8">
<title>Tidewater Sleeve – Envelope Dieline</title>
<link rel="stylesheet" href="https://fonts.googleapis.com/css2?family=Montserrat:wght@200;800&display=swap">
<style>
  :root {
    --paper: #ffffff;
    --leaf: #52ff00;
    --ink: #333333;
    --white: #ffffff;
    --cut-edge: #e8322b;
    --crop: #000000;
  }
  * { margin: 0; padding: 0; box-sizing: border-box; }
  html, body { width: 1200px; height: 861px; overflow: hidden; background: var(--paper); }
  .sheet { position: relative; width: 1200px; height: 861px; font-family: "Montserrat", sans-serif; }
  .dieline { position: absolute; inset: 0; }

  .flap-label {
    position: absolute; top: 154px; width: 220px; margin-left: -110px;
    text-align: center; font-weight: 200; font-size: 44px; line-height: 1;
    color: var(--white); transform: rotate(180deg);
  }
  .flap-label--body { left: 317px; }
  .flap-label--mind { left: 603px; }
  .flap-label--spirit { left: 897px; }

  .brand-tag {
    position: absolute; left: 755px; top: 241px; width: 122px; height: 51px;
    background: var(--white); display: flex; align-items: center; justify-content: flex-end;
    padding-right: 9px; gap: 5px;
    font-weight: 800; font-size: 14px; color: var(--leaf);
  }
  .brand-tag__dot { width: 18px; height: 18px; border-radius: 50%; background: var(--leaf); }

  .question {
    position: absolute; left: 455px; top: 291px; width: 297px;
    text-align: center; font-weight: 800; font-size: 41px; line-height: 44px;
    color: var(--ink); letter-spacing: -0.3px;
  }
  .question__accent { color: var(--white); }

  .product-title {
    position: absolute; left: 752px; top: 373px; width: 289px;
    text-align: center; font-weight: 800; font-size: 43px; line-height: 43px;
    color: var(--ink);
  }
  .product-title__accent { color: var(--white); }

  .tile { position: absolute; border-radius: 9px; }
  .tile--lg { width: 62px; height: 62px; top: 559px; }
  .tile--sm { width: 49px; height: 49px; top: 660px; border-radius: 7px; }
  .tile--body { background: linear-gradient(180deg, #c9d6f0 0%, #e9c6a8 55%, #f29a26 80%, #4a3a2c 100%); }
  .tile--mind { background: radial-gradient(circle at 55% 50%, #f0542c 0%, #d43a8a 30%, #1a6ee8 60%, #0b2a9a 100%); }
  .tile--spirit { background: linear-gradient(180deg, #5d7fae 0%, #e9a26a 45%, #c98a5a 55%, #34506f 100%); }
  .tile--flip { transform: rotate(180deg); }
</style>
</head>
<body>
<main class="sheet">
  <svg class="dieline" width="1200" height="861" viewBox="0 0 1200 861" aria-hidden="true">
    <g fill="var(--leaf)">
      <rect x="158" y="218" width="883" height="427"/>
      <rect x="81" y="588" width="78" height="57"/>
      <rect x="1040" y="588" width="78" height="57"/>
      <polygon points="158,218 179,141 449,141 455,218"/>
      <rect x="455" y="141" width="297" height="78"/>
      <polygon points="752,218 759,141 1021,141 1041,218"/>
      <polygon points="158,645 179,722 449,722 455,645"/>
      <rect x="455" y="644" width="297" height="78"/>
      <polygon points="752,645 759,722 1021,722 1041,645"/>
    </g>
    <g stroke="var(--cut-edge)" stroke-width="0.6" fill="none">
      <path d="M158 218 L179 141 M449 141 L455 218 M752 218 L759 141 M1021 141 L1041 218"/>
      <path d="M158 645 L179 722 M449 722 L455 645 M752 645 L759 722 M1021 722 L1041 645"/>
    </g>
    <g stroke="var(--crop)" stroke-width="0.7" fill="none">
      <path d="M129 141 H158 V112 M1041 112 V141 H1070"/>
      <path d="M129 722 H158 V751 M1041 751 V722 H1070"/>
      <path d="M129 218 H158 M1041 218 H1070"/>
      <path d="M455 112 V141 M752 112 V141 M455 722 V751 M752 722 V751"/>
      <path d="M52 588 H81 M52 645 H81 M1118 588 H1147 M1118 645 H1147"/>
    </g>
  </svg>

  <p class="flap-label flap-label--body">Body</p>
  <p class="flap-label flap-label--mind">Mind</p>
  <p class="flap-label flap-label--spirit">Spirit</p>

  <div class="brand-tag"><span>VANTIRO</span><span class="brand-tag__dot"></span></div>

  <h2 class="question">Know<br>someone<br>who<br>needs<br><span class="question__accent">Healing?</span></h2>

  <h1 class="product-title"><span class="product-title__accent">Tidewater</span><br>Sleeve</h1>

  <div class="tile tile--lg tile--body" style="left:482px" role="img" aria-label="Runner leaping at sunset"></div>
  <div class="tile tile--lg tile--mind" style="left:571px" role="img" aria-label="Glowing brain inside a head profile"></div>
  <div class="tile tile--lg tile--spirit" style="left:660px" role="img" aria-label="Sunrise over a calm mountain lake"></div>
  <div class="tile tile--lg tile--body" style="left:775px" role="img" aria-label="Runner leaping at sunset"></div>
  <div class="tile tile--lg tile--mind" style="left:864px" role="img" aria-label="Glowing brain inside a head profile"></div>
  <div class="tile tile--lg tile--spirit" style="left:954px" role="img" aria-label="Sunrise over a calm mountain lake"></div>

  <div class="tile tile--sm tile--body tile--flip" style="left:277px" role="img" aria-label="Runner leaping at sunset"></div>
  <div class="tile tile--sm tile--mind tile--flip" style="left:579px" role="img" aria-label="Glowing brain inside a head profile"></div>
  <div class="tile tile--sm tile--spirit tile--flip" style="left:871px" role="img" aria-label="Sunrise over a calm mountain lake"></div>
</main>
</body>
</html>
```